Home Remodeling company needs a business card design

we need a business card design for home remodeling company in hamilton county, indiana USA. we offers a wide range of construction services including whole house renovations, Design and Build Basements and Kitchen and Bathroom Remodeling . we would like to see designs for both site of business card that use the same color of the company logo and also including all information below :
1- Karim Feltous CEO / General Contractor
2- all company contacts Telephone numbers ( 1-888-DULOM-47 ) ( 317-555-0193) email address ( info@dulomhome.com) website ( www.dulomhome.com ) and social media logos (Facebook- twitter- google plus )
3- company logo
4- licensed . insured . bonded

```html
<!DOCTYPE html>
<html lang="en">
<head>
<meta charset="utf-8">
<title>Dulom Home Remodeling – Business Card</title>
<link href="https://fonts.googleapis.com/css2?family=Roboto:wght@400;700&display=swap" rel="stylesheet">
<style>
  :root{
    --bg:#3b322e;
    --card:#f7f7f7;
    --ink:#3a3a3a;
    --soft:#555555;
    --red:#c8202f;
  }
  *{margin:0;padding:0;box-sizing:border-box}
  html,body{width:1200px;height:716px;overflow:hidden}
  body{background:var(--bg);font-family:"Roboto",Arial,sans-serif;color:var(--ink)}
  .stage{position:relative;width:1200px;height:716px}
  .card{position:absolute;top:215px;width:500px;height:286px;background:var(--card);box-shadow:0 10px 30px rgba(0,0,0,.35)}
  .card--front{left:70px}
  .card--back{left:630px}

  .company-name{position:absolute;font-family:"Roboto",Arial,sans-serif;font-weight:700;color:var(--ink);white-space:nowrap}
  .card--front .company-name{left:50%;top:50%;transform:translate(-50%,-50%);font-size:30px}
  .card--back .company-name{right:30px;top:96px;font-size:24px}

  .person{position:absolute;left:32px;top:28px}
  .person__name{color:var(--red);font-weight:700;font-size:17px}
  .person__role{font-size:10.5px;color:var(--soft);margin-top:3px}

  .contacts{position:absolute;left:32px;top:168px;list-style:none}
  .contacts li{display:flex;align-items:center;gap:10px;font-size:13px;height:20px;color:var(--ink)}
  .contacts svg{width:11px;height:11px;fill:var(--red);flex:none}

  .footer{position:absolute;right:30px;bottom:26px;text-align:right}
  .follow{display:flex;align-items:center;justify-content:flex-end;gap:5px}
  .follow__label{color:var(--red);font-size:14px;margin-right:4px}
  .follow__box{width:18px;height:18px;background:var(--ink)}
  .creds{margin-top:6px;font-size:14.5px;color:var(--ink)}
  .creds .dot{color:var(--red);margin:0 6px}
</style>
</head>
<body>
<main class="stage">
  <section class="card card--front" aria-label="Card front">
    <p class="company-name">Dulom Home Remodeling</p>
  </section>

  <section class="card card--back" aria-label="Card back">
    <div class="person">
      <p class="person__name">Karim Feltous</p>
      <p class="person__role">CEO / General Contractor</p>
    </div>

    <p class="company-name">Dulom Home Remodeling</p>

    <ul class="contacts">
      <li><svg viewBox="0 0 24 24"><path d="M6.6 10.8a15 15 0 0 0 6.6 6.6l2.2-2.2a1 1 0 0 1 1-.25 11 11 0 0 0 3.6.6 1 1 0 0 1 1 1V20a1 1 0 0 1-1 1A17 17 0 0 1 3 4a1 1 0 0 1 1-1h3.5a1 1 0 0 1 1 1 11 11 0 0 0 .6 3.6 1 1 0 0 1-.25 1z"/></svg>1-888-DULOM-47</li>
      <li><svg viewBox="0 0 24 24"><path d="M4 9c0-3 4-5 8-5s8 2 8 5v2h-4V9H8v2H4zM6 12h12l2 8H4zm6 2a2 2 0 1 0 0 4 2 2 0 0 0 0-4z"/></svg>317-555-0193</li>
      <li><svg viewBox="0 0 24 24"><path d="M2 5h20v14H2zm2 2v.5l8 5 8-5V7zm0 3v7h16v-7l-8 5z"/></svg>info@dulomhome.com</li>
      <li><svg viewBox="0 0 24 24"><path d="M12 2a10 10 0 1 0 0 20 10 10 0 0 0 0-20zm0 2c1.2 1.4 2 3.5 2.2 7H9.8C10 7.5 10.8 5.4 12 4zM4.1 11a8 8 0 0 1 4.2-6.1C7.6 6.6 7.2 8.7 7.8 11zm0 2h3.7c-.1 2.3.4 4.4 1 6.1A8 8 0 0 1 4.1 13zm5.7 0h4.4c-.2 3.5-1 5.6-2.2 7-1.2-1.4-2-3.5-2.2-7zm6.4 0h3.7a8 8 0 0 1-4.2 6.1c.6-1.7 1-3.8.5-6.1zm0-2c0-2.3-.4-4.4-1-6.1a8 8 0 0 1 4.7 6.1z"/></svg>www.dulomhome.com</li>
    </ul>

    <div class="footer">
      <div class="follow">
        <span class="follow__label">Follows on:</span>
        <span class="follow__box" aria-label="Social network"></span>
        <span class="follow__box" aria-label="Social network"></span>
        <span class="follow__box" aria-label="Social network"></span>
      </div>
      <p class="creds">Licensed<span class="dot">•</span>Insured<span class="dot">•</span>Bonded</p>
    </div>
  </section>
</main>
</body>
</html>
```